SnackOrbit!!! A Vending Machine Business Looking for an attractive website.

We are a vending machine business in Northern Michigan. We have changed our name and have rebranded our company. We would like an attractive website that shares who we are, what services we provide, the products we offer in our machines, along with a form businesses can fill out to see if they are a good fit for our company. I would like to have a Home Page, About SnackOrbit, Why Choose SnackOrbit?, Products & Services, Contact Us (With a Login Option), and a page with a questionnaire for thos interested in getting a FREE Vending Machine.

Target Market(s)

Businesses, Campgrounds, Schools, and many more in Northern Michigan

Industry/Entity Type

Vending Machines

Coding

Coded - Design and coding required

Number of Pages Required

5+ page

Requirements
Must have
• An inviting and enticing Home Page. I want to get my potential clients engaged in our website.
Nice to have
• Possibly background photos from Northern Michigan
Should not have
• A corporate feel. I do not want a boring website.

```html
<!DOCTYPE html>
<html lang="en">
<head>
<meta charset="utf-8">
<title>SnackOrbit – Crave. Vend. Repeat.</title>
<link href="https://fonts.googleapis.com/css2?family=Russo+One&family=Roboto:wght@400;500;700&display=swap" rel="stylesheet">
<style>
:root{
  --navy:#1c2262;
  --green:#2d5a27;
  --ink:#222;
  --muted:#555;
  --light:#f2f3f6;
  --footer:#0e0f1a;
  --white:#fff;
}
*{margin:0;padding:0;box-sizing:border-box}
html,body{width:1200px;height:3254px;overflow:hidden}
body{position:relative;font-family:"Roboto",sans-serif;color:var(--ink);background:var(--white)}
.abs{position:absolute}
.display{font-family:"Russo One",sans-serif;font-weight:400}
.btn{position:absolute;display:flex;align-items:center;justify-content:center;gap:12px;background:var(--green);color:var(--white);font-weight:700;font-size:15px;text-transform:uppercase;letter-spacing:.2px}
.btn svg{width:24px;height:10px}
.social{display:flex;gap:6px}
.social span{width:27px;height:27px;border:1.5px solid #333;border-radius:50%}

/* header */
.site-header{top:0;left:0;width:1200px;height:103px;background:var(--white)}
.brand{left:144px;top:22px;display:flex;align-items:center;gap:10px;font-family:"Russo One",sans-serif;font-size:38px;color:var(--navy)}
.brand-dot{width:26px;height:26px;border-radius:50%;background:var(--green)}
.follow{left:595px;top:17px;display:flex;align-items:center;gap:12px;font-size:12px;font-weight:500}
.cta-top{left:830px;top:11px;width:225px;height:37px;font-size:13px}
.nav{left:402px;top:68px;display:flex;gap:36px;font-size:15px;font-weight:500}
.nav a{color:var(--ink);text-decoration:none;padding-bottom:6px}
.nav a.active{border-bottom:2px solid var(--navy)}

/* hero */
.hero-photo{top:103px;left:0;width:1200px;height:600px;background:linear-gradient(90deg,#dfe4e2 0%,#b9c2bd 30%,#8f918b 48%,#3d3f42 55%,#c58a3d 62%,#6e5c3f 80%,#2d2a27 100%)}
.hero-title{left:144px;top:226px;font-size:46px;line-height:60px;color:#111}
.hero-sub{left:145px;top:363px;font-size:16px;color:#111}
.hero-btn{left:144px;top:416px;width:193px;height:48px}

/* about */
.about-block{left:384px;top:775px;width:173px;height:151px;background:var(--green)}
.about-dots{left:126px;top:960px;width:212px;height:212px;background-image:radial-gradient(var(--navy) 1.2px,transparent 1.4px);background-size:6px 6px}
.about-photo{left:144px;top:792px;width:397px;height:363px;background:linear-gradient(135deg,#c9cfd4,#8a7a68 55%,#6c6358)}
.about-title{left:619px;top:812px;font-size:36px;color:#111}
.about-title em{font-style:normal;color:var(--navy)}
.about-text{left:620px;top:873px;width:435px;font-size:13.5px;line-height:24px;color:var(--muted);text-align:justify}
.about-text p+p{margin-top:8px}
.about-btn{left:621px;top:1081px;width:162px;height:46px}

/* why */
.why{top:1271px;left:0;width:1200px;height:678px;background:linear-gradient(90deg,#f4f5f8 0%,#eef0f4 45%,#dcdfe3 55%,#9aa3a7 70%,#c9a66b 100%)}
.why-photo{top:1271px;left:594px;width:606px;height:678px;background:linear-gradient(160deg,#d8dadc 0%,#a8b0b4 35%,#3c8a5d 60%,#c7ae7e 100%)}
.why-title{left:142px;top:1320px;font-size:32px;color:var(--navy)}
.why-intro{left:144px;top:1372px;width:420px;font-size:13.5px;line-height:22px;color:var(--muted)}
.feature{left:140px;width:440px;display:flex;gap:22px}
.feature svg{flex:0 0 46px;height:50px}
.feature h3{font-size:17px;font-weight:500;color:var(--navy);margin-bottom:6px}
.feature p{font-size:13.5px;line-height:24px;color:var(--muted)}
.why-btn{left:142px;top:1850px;width:162px;height:46px}

/* cta band */
.band{top:1949px;left:0;width:1200px;height:317px;background:var(--navy);color:var(--white);text-align:center}
.band h2{position:absolute;top:55px;width:100%;font-family:"Russo One",sans-serif;font-weight:400;font-size:32px}
.band p{position:absolute;top:118px;width:100%;font-size:18px;line-height:28px;font-weight:500}
.call{position:absolute;left:477px;top:207px;width:246px;height:46px;background:var(--white);border-radius:23px;display:flex;align-items:center;gap:12px;padding-left:4px;color:var(--navy);font-weight:500;font-size:14.5px}
.call i{width:38px;height:38px;border-radius:50%;background:var(--green);display:flex;align-items:center;justify-content:center}

/* products */
.products{top:2266px;left:0;width:1200px;height:658px;background:linear-gradient(180deg,#fff 0%,#fff 35%,#e8e4ea 60%,#c9bfc0 80%,#d9d5da 100%)}
.products-title{top:2330px;width:1200px;left:0;text-align:center;font-size:38px;color:var(--navy)}
.products-title em{font-style:normal;color:var(--green)}
.products-intro{top:2404px;left:140px;width:920px;text-align:center;font-size:15px;line-height:25px;color:var(--muted)}
.card{top:2489px;width:210px;text-align:center}
.card-img{height:264px;background:var(--white);display:flex;align-items:center;justify-content:center}
.card-img div{width:120px;height:220px;border-radius:4px;background:linear-gradient(180deg,#3a3a3e,#7d6a55 50%,#2c2c30)}
.card h4{margin-top:18px;font-size:16px;font-weight:500}
.card p{font-size:14px;margin-top:4px}
.card b{display:inline-block;margin-top:8px;font-size:16px;font-weight:500;color:var(--navy);border-bottom:1.5px solid var(--navy)}
.arrow{top:2608px;width:24px;height:24px;border:1.3px solid #555;border-radius:50%}

/* footer */
.footer{top:2924px;left:0;width:1200px;height:330px;background:var(--footer);color:var(--white)}
.footer .brand{left:134px;top:62px;color:var(--white)}
.footer .brand-dot{background:var(--white)}
.f-follow{left:145px;top:171px;display:flex;align-items:center;gap:12px;font-size:12px;font-weight:500}
.f-follow .social span{border-color:var(--white)}
.f-col{top:76px}
.f-col h5{font-size:17px;font-weight:700;margin-bottom:14px}
.f-col li{list-style:none;font-size:12px;line-height:24px}
.f-col li svg{width:10px;height:10px;margin-right:8px;vertical-align:-1px}
.copyright{top:302px;left:0;width:1200px;text-align:center;font-size:12px}
</style>
</head>
<body>

<header class="abs site-header">
  <div class="abs brand"><span class="brand-dot"></span>SnackOrbit</div>
  <div class="abs follow">FOLLOW US:
    <div class="social"><span></span><span></span><span></span><span></span></div>
  </div>
  <div class="btn cta-top">Get a free vending machine</div>
  <nav class="abs nav">
    <a class="active">Home</a><a>About SnackOrbit</a><a>Why Choose SnackOrbit?</a><a>Products &amp; Services</a><a>Contact Us</a>
  </nav>
</header>

<section>
  <div class="abs hero-photo" role="img" aria-label="Stocked snack vending machine in a bright lobby"></div>
  <h1 class="abs display hero-title">SnackOrbit – Crave.<br>Vend. Repeat.</h1>
  <p class="abs hero-sub">Elevating Snacking, One Vend at a Time.</p>
  <div class="btn hero-btn">Get started <svg viewBox="0 0 24 10"><path d="M0 5h22M17 1l5 4-5 4" stroke="#fff" fill="none" stroke-width="1.5"/></svg></div>
</section>

<section>
  <div class="abs about-block"></div>
  <div class="abs about-dots"></div>
  <div class="abs about-photo" role="img" aria-label="White drink vending machine beside a brick wall on a city street"></div>
  <h2 class="abs display about-title">About <em>us</em></h2>
  <div class="abs about-text">
    <p>Welcome to SnackOrbit, where snacking meets delight! We're not just about vending machines, we're your culinary companions, your flavor curators, and your secret stash of happiness. Owen and Clara, the dynamic duo behind SnackOrbit, have a passion for all things tasty.</p>
    <p>With backgrounds in sales and a penchant for personal connections, they've transformed the vending experience into an art form. delight with every bite.Whether you're reaching for a mid-morning.</p>
  </div>
  <div class="btn about-btn">Read more <svg viewBox="0 0 24 10"><path d="M0 5h22M17 1l5 4-5 4" stroke="#fff" fill="none" stroke-width="1.5"/></svg></div>
</section>

<section>
  <div class="abs why"></div>
  <div class="abs why-photo" role="img" aria-label="Smiling woman choosing a snack on a touchscreen vending machine"></div>
  <h2 class="abs display why-title">Why Choose SnackOrbit?</h2>
  <p class="abs why-intro">At SnackOrbit, we're more than vending machines; we're flavor architects, community connectors, and taste trailblazers. Imagine a world where every snack is an adventure, every sip a celebration.</p>

  <div class="abs feature" style="top:1458px">
    <svg viewBox="0 0 46 50"><path d="M23 48C10 34 5 26 5 19a18 18 0 0 1 36 0c0 7-5 15-18 29z" fill="none" stroke="#1c2262" stroke-width="2.5"/><path d="M23 28l-7-7a4 4 0 0 1 7-4 4 4 0 0 1 7 4z" fill="none" stroke="#2d5a27" stroke-width="2.2"/></svg>
    <div><h3>LOCAL LOVE</h3><p>We celebrate the heart of Michigan by partnering with local legends. Say hello to Pine Ridge Jerky.</p></div>
  </div>
  <div class="abs feature" style="top:1554px">
    <svg viewBox="0 0 46 50"><rect x="8" y="3" width="30" height="44" rx="2" fill="none" stroke="#1c2262" stroke-width="2.2"/><path d="M12 10h16M12 18h16M12 26h16M12 34h16M12 41h22" stroke="#1c2262" stroke-width="2"/><path d="M32 10v20" stroke="#2d5a27" stroke-width="2.2"/></svg>
    <div><h3>UNLEASH YOUR CRAVINGS</h3><p>SnackOrbit isn't bound by corporate ties, We're the rebels of the vending world. Craving a bag of crispy.</p></div>
  </div>
  <div class="abs feature" style="top:1648px">
    <svg viewBox="0 0 46 50"><circle cx="23" cy="19" r="15" fill="none" stroke="#1c2262" stroke-width="2.2"/><path d="M16 19l5 5 9-10" fill="none" stroke="#2d5a27" stroke-width="2.5"/><path d="M13 31l-5 15 6-3 3 5 5-12M33 31l5 15-6-3-3 5-5-12" fill="none" stroke="#1c2262" stroke-width="2"/></svg>
    <div><h3>QUALITY MEETS CONVENIENCE</h3><p>Imagine this: You're mid-meeting, and your stomach growls. Fear not! SnackOrbit's machines offer top-notch.</p></div>
  </div>
  <div class="abs feature" style="top:1744px">
    <svg viewBox="0 0 46 50"><circle cx="23" cy="25" r="21" fill="none" stroke="#2d5a27" stroke-width="2.5"/><path d="M14 24h5v12h-5zM19 25l5-9c2 0 3 2 2 5h7c2 0 3 2 2 4l-3 9c-1 2-2 2-3 2h-10" fill="none" stroke="#1c2262" stroke-width="2"/></svg>
    <div><h3>PANDEMIC-PROOF &amp; RECESSION-READY</h3><p>Life throws curveballs, but SnackOrbit stands strong.<br>Our vending machines are the unsung heroes of resilience.</p></div>
  </div>
  <div class="btn why-btn">Read more <svg viewBox="0 0 24 10"><path d="M0 5h22M17 1l5 4-5 4" stroke="#fff" fill="none" stroke-width="1.5"/></svg></div>
</section>

<section class="abs band">
  <h2>Ready To Experience The SnackOrbit Difference?</h2>
  <p>Sign up now and let's connect. Taste the future of snacking firsthand! Contact us today<br>and explore how our vending magic can elevate your space.</p>
  <div class="call"><i><svg width="16" height="16" viewBox="0 0 24 24"><path d="M6.6 10.8a15 15 0 0 0 6.6 6.6l2.2-2.2c.3-.3.7-.4 1-.2 1.1.4 2.3.6 3.6.6.6 0 1 .4 1 1V20c0 .6-.4 1-1 1A17 17 0 0 1 3 4c0-.6.4-1 1-1h3.5c.6 0 1 .4 1 1 0 1.3.2 2.5.6 3.6.1.3 0 .7-.2 1z" fill="#fff"/></svg></i>CALL US AT 555-014-2277</div>
</section>

<section>
  <div class="abs products" role="img" aria-label="Soft sunset shoreline background"></div>
  <h2 class="abs display products-title"><em>Products</em> &amp; Services</h2>
  <p class="abs products-intro">We're not just about vending machines; we're your culinary companions, your flavor curators, and your secret stash of happiness.We're the ones who believe that a vending machine isn't just a metal box; it's a portal to delight.</p>
  <div class="abs arrow" style="left:68px"></div>
  <div class="abs arrow" style="left:1107px"></div>
  <div class="abs card" style="left:144px"><div class="card-img"><div role="img" aria-label="Black snack vending machine"></div></div><h4>PRODUCT 01</h4><p>Special Offers Available</p><b>$ 6999</b></div>
  <div class="abs card" style="left:378px"><div class="card-img"><div role="img" aria-label="Black snack vending machine, angled"></div></div><h4>PRODUCT 01</h4><p>Special Offers Available</p><b>$ 6999</b></div>
  <div class="abs card" style="left:612px"><div class="card-img"><div role="img" aria-label="Silver snack vending machine"></div></div><h4>PRODUCT 01</h4><p>Special Offers Available</p><b>$ 6999</b></div>
  <div class="abs card" style="left:845px"><div class="card-img"><div role="img" aria-label="Teal and white snack vending machine" style="background:linear-gradient(180deg,#e9eef0,#d98b6a 45%,#33c0c0)"></div></div><h4>PRODUCT 01</h4><p>Special Offers Available</p><b>$ 6999</b></div>
</section>

<footer class="abs footer">
  <div class="abs brand"><span class="brand-dot"></span>SnackOrbit</div>
  <div class="abs f-follow">FOLLOW US:
    <div class="social"><span></span><span></span><span></span><span></span></div>
  </div>
  <div class="abs f-col" style="left:450px"><h5>QUICK LINKS</h5><ul><li>Home</li><li>About SnackOrbit</li><li>Why Choose SnackOrbit?</li><li>Products &amp; Services</li><li>Contact Us</li></ul></div>
  <div class="abs f-col" style="left:669px"><h5>ABOUT COMPANY</h5><ul><li>Our Company</li><li>Term of Services</li><li>Privacy Policy</li><li>Latest News</li><li>Site Map</li></ul></div>
  <div class="abs f-col" style="left:891px"><h5>CONTACT US</h5><ul>
    <li><svg viewBox="0 0 10 10"><path d="M5 10C2 6 1 5 1 4a4 4 0 0 1 8 0c0 1-1 2-4 6z" fill="#fff"/></svg>Lorem ipsum dolor sit amet.</li>
    <li><svg viewBox="0 0 24 24"><path d="M6.6 10.8a15 15 0 0 0 6.6 6.6l2.2-2.2c.3-.3.7-.4 1-.2 1.1.4 2.3.6 3.6.6.6 0 1 .4 1 1V20c0 .6-.4 1-1 1A17 17 0 0 1 3 4c0-.6.4-1 1-1h3.5c.6 0 1 .4 1 1 0 1.3.2 2.5.6 3.6.1.3 0 .7-.2 1z" fill="#fff"/></svg>+1 555 014 2277</li>
    <li style="margin-top:6px"><svg viewBox="0 0 10 8"><rect width="10" height="8" fill="#fff"/><path d="M0 0l5 4 5-4" stroke="#0e0f1a" fill="none"/></svg>info@snackorbit.com</li>
  </ul></div>
  <p class="abs copyright">© Copyright 2024 &nbsp;/ SnackOrbit / All Rights Reserved</p>
</footer>

</body>
</html>
```